Walk Beside The River

Business Card design

Target Market(s)

People who require support in the commnity

Industry/Entity Type

Mental Health Support

Contact Information for Business Card

Mental Health Support Rosalind Tavener walkbesidetheriver@mailcove.com.au 0481 637 092 PO Box 926 Maroochydore QLD 4558

Colors
6B429C
8869AF
B7A5CE
E3DAEB
F3F0F8

Requirements
Must have
• Logo & details listed above
Should not have
• No red or orange

```html
<!DOCTYPE html>
<html lang="en">
<head>
<meta charset="utf-8">
<title>Walk Beside The River – Business Card</title>
<link rel="stylesheet" href="https://fonts.googleapis.com/css2?family=Open+Sans:wght@400;600;700&display=swap">
<style>
  :root {
    --stage: #2c2c30;
    --card: #222127;
    --card-back: #1e1d22;
    --purple: #6b429c;
    --yellow: #e6e02a;
    --white: #f3f0f8;
    --emboss: #2e2d34;
  }
  * { box-sizing: border-box; margin: 0; padding: 0; }
  html, body {
    width: 1200px; height: 780px; overflow: hidden;
    background: var(--stage);
    font-family: "Open Sans", Arial, sans-serif;
  }
  .stage {
    width: 1200px; height: 780px;
    display: flex; align-items: center; justify-content: center; gap: 50px;
  }
  .card {
    position: relative;
    width: 525px; height: 300px;
    overflow: hidden;
    box-shadow: 0 14px 30px rgba(0,0,0,.45);
  }
  .card--front { background: var(--card); }
  .card--back {
    background: var(--card-back);
    display: flex; align-items: center; justify-content: center;
  }

  .brand {
    position: absolute; left: 34px; top: 26px;
    display: flex; align-items: center; gap: 14px;
  }
  .brand__mark {
    width: 74px; height: 74px; border-radius: 50%;
    background: var(--purple);
  }
  .brand__name {
    color: var(--white); font-weight: 600; font-size: 15px;
    letter-spacing: .08em; text-transform: uppercase; line-height: 1.35;
  }

  .details {
    position: absolute; left: 34px; top: 124px;
    color: var(--white); font-size: 13.5px; line-height: 1.55;
  }
  .details__line { display: flex; align-items: center; gap: 8px; white-space: nowrap; }
  .details__line svg { width: 13px; height: 13px; flex: none; }
  .details__list { margin-top: 2px; }

  .person {
    position: absolute; right: 40px; bottom: 34px; text-align: right;
  }
  .person__name { color: var(--yellow); font-weight: 700; font-size: 27px; line-height: 1.15; }
  .person__role { color: var(--white); font-size: 15px; margin-top: 2px; }

  .accent-bar {
    position: absolute; right: 0; bottom: 40px;
    width: 16px; height: 52px; background: var(--yellow);
  }

  .back__name {
    color: var(--emboss); font-weight: 700; font-size: 26px;
    letter-spacing: .1em; text-transform: uppercase; text-align: center; line-height: 1.3;
  }
</style>
</head>
<body>
<main class="stage">
  <section class="card card--front" aria-label="Business card front">
    <div class="brand">
      <span class="brand__mark" aria-hidden="true"></span>
      <span class="brand__name">Walk Beside<br>The River</span>
    </div>

    <div class="details">
      <p>Mental Health Support</p>
      <p>Rosalind Tavener</p>
      <div class="details__list">
        <p class="details__line">
          <svg viewBox="0 0 16 16" aria-hidden="true"><path d="M4 1.5 6.5 4.5 5 6.2c.8 1.9 2.4 3.6 4.3 4.4l1.6-1.5 3 2.5-1.4 2.4C7.5 14 2 8.5 1.6 3z" fill="none" stroke="#e6e02a" stroke-width="1.6" stroke-linejoin="round"/></svg>
          0481 637 092
        </p>
        <p class="details__line">
          <svg viewBox="0 0 16 16" aria-hidden="true"><rect x="1.5" y="3.5" width="13" height="9.5" fill="none" stroke="#e6e02a" stroke-width="1.6"/><path d="M1.5 3.5 8 9l6.5-5.5" fill="none" stroke="#e6e02a" stroke-width="1.6"/></svg>
          walkbesidetheriver@mailcove.com.au
        </p>
        <p class="details__line">
          <svg viewBox="0 0 16 16" aria-hidden="true"><path d="M8 15s5-5 5-9A5 5 0 0 0 3 6c0 4 5 9 5 9z" fill="none" stroke="#e6e02a" stroke-width="1.6"/><circle cx="8" cy="6" r="1.8" fill="#e6e02a"/></svg>
          PO Box 926 Riverglen QLD 4999
        </p>
      </div>
    </div>

    <div class="person">
      <p class="person__name">Ilona Varga</p>
      <p class="person__role">CEO/Director</p>
    </div>
    <span class="accent-bar" aria-hidden="true"></span>
  </section>

  <section class="card card--back" aria-label="Business card back">
    <p class="back__name">Walk Beside<br>The River</p>
  </section>
</main>
</body>
</html>
```